New Business Card Design Project

Use the flyer uploaded and website www.brightoakbuilders.com for inspiration.
List Our Services on Backside of business cards
Marcus Delling
Harborline Builders Inc.
Licensed General Contractors
858-471-6093

Contact Information for Business Card

Use the flyer uploaded and website www.brightoakbuilders.com for inspiration. List Our Services on Backside of business cards Marcus Delling Harborline Builders Inc. Licensed General Contractors 858-471-6093

```html
<!DOCTYPE html>
<html lang="en">
<head>
<meta charset="utf-8">
<title>Harborline Builders – Business Card</title>
<link rel="stylesheet" href="https://fonts.googleapis.com/css2?family=Montserrat:wght@500;600&family=Roboto:wght@500;700;900&display=swap">
<style>
  :root {
    --page: #232323;
    --card: #1f1f21;
    --card-back: #202024;
    --red: #e3161f;
    --blue: #5a7fca;
    --white: #f4f4f4;
  }
  * { margin: 0; padding: 0; box-sizing: border-box; }
  html, body { width: 1200px; height: 780px; overflow: hidden; background: var(--page); }
  .canvas { position: relative; width: 1200px; height: 780px; }

  .card {
    position: absolute; width: 560px; height: 320px;
    background: var(--card);
    border-bottom: 6px solid var(--red);
    box-shadow: 0 14px 30px rgba(0,0,0,.55);
    overflow: hidden;
  }
  .card--services { left: 40px; top: 90px; }
  .card--contact { left: 600px; top: 370px; background: var(--card-back); }

  /* Services side */
  .brand {
    position: absolute; top: 56px; left: 0; right: 0;
    display: flex; justify-content: center; align-items: center; gap: 14px;
  }
  .brand__mark { width: 14px; height: 14px; background: var(--white); }
  .brand__name {
    font-family: "Montserrat", sans-serif; font-weight: 500;
    font-size: 30px; letter-spacing: 3px; color: var(--white); text-transform: uppercase;
  }
  .services { position: absolute; top: 146px; left: 0; right: 0; text-align: center; }
  .services__guarantee {
    font-family: "Roboto", sans-serif; font-weight: 900; font-size: 15px;
    color: var(--red); letter-spacing: .3px;
  }
  .services__heading {
    font-family: "Roboto", sans-serif; font-weight: 900; font-size: 14px;
    color: var(--blue); margin-top: 2px; letter-spacing: .4px;
  }
  .services__list {
    list-style: none; margin-top: 12px;
    display: flex; flex-wrap: wrap; justify-content: center;
    column-gap: 10px; row-gap: 5px; padding: 0 22px;
    font-family: "Montserrat", sans-serif; font-weight: 500; font-size: 11.5px; color: var(--white);
  }
  .services__list li { display: flex; align-items: center; gap: 4px; white-space: nowrap; }
  .tick { width: 11px; height: 11px; flex: none; }

  /* Contact side */
  .person { position: absolute; left: 46px; top: 170px; }
  .person__name {
    font-family: "Roboto", sans-serif; font-weight: 900; font-size: 38px;
    color: var(--red); line-height: 1;
  }
  .person__title {
    font-family: "Montserrat", sans-serif; font-weight: 500; font-size: 13.5px;
    color: var(--white); margin-top: 4px;
  }
  .divider { position: absolute; left: 322px; top: 92px; width: 1.5px; height: 108px; background: var(--red); }
  .contacts {
    position: absolute; left: 348px; top: 104px; list-style: none;
    font-family: "Montserrat", sans-serif; font-weight: 500; font-size: 12.5px; color: var(--white);
  }
  .contacts li { display: flex; align-items: center; gap: 8px; margin-bottom: 9px; }
  .contacts svg { width: 14px; height: 14px; flex: none; }
  .company {
    position: absolute; left: 300px; bottom: 30px;
    font-family: "Montserrat", sans-serif; font-weight: 500; font-size: 13.5px; color: var(--white);
  }
</style>
</head>
<body>
<main class="canvas">

  <section class="card card--services" aria-label="Business card, services side">
    <div class="brand">
      <span class="brand__mark"></span>
      <span class="brand__name">Harborline Builders</span>
    </div>
    <div class="services">
      <p class="services__guarantee">OUR SERVICES ARE 100% GUARANTEED</p>
      <p class="services__heading">SPECIALIZING IN:</p>
      <ul class="services__list">
        <li><svg class="tick" viewBox="0 0 12 12"><circle cx="6" cy="6" r="5" fill="none" stroke="#e3161f" stroke-width="1.2"/><path d="M3.5 6.2l1.8 1.8 3.4-3.8" fill="none" stroke="#e3161f" stroke-width="1.3"/></svg>Remodel: Kitchen &amp; Bath</li>
        <li><svg class="tick" viewBox="0 0 12 12"><circle cx="6" cy="6" r="5" fill="none" stroke="#e3161f" stroke-width="1.2"/><path d="M3.5 6.2l1.8 1.8 3.4-3.8" fill="none" stroke="#e3161f" stroke-width="1.3"/></svg>Painting: Interior &amp; Exterior</li>
        <li><svg class="tick" viewBox="0 0 12 12"><circle cx="6" cy="6" r="5" fill="none" stroke="#e3161f" stroke-width="1.2"/><path d="M3.5 6.2l1.8 1.8 3.4-3.8" fill="none" stroke="#e3161f" stroke-width="1.3"/></svg>Flooring: Carpet, Vinyl, Wood</li>
        <li><svg class="tick" viewBox="0 0 12 12"><circle cx="6" cy="6" r="5" fill="none" stroke="#e3161f" stroke-width="1.2"/><path d="M3.5 6.2l1.8 1.8 3.4-3.8" fill="none" stroke="#e3161f" stroke-width="1.3"/></svg>Window &amp; Door Replacement</li>
        <li><svg class="tick" viewBox="0 0 12 12"><circle cx="6" cy="6" r="5" fill="none" stroke="#e3161f" stroke-width="1.2"/><path d="M3.5 6.2l1.8 1.8 3.4-3.8" fill="none" stroke="#e3161f" stroke-width="1.3"/></svg>Plumbing: Repairs &amp; Upgrades</li>
        <li><svg class="tick" viewBox="0 0 12 12"><circle cx="6" cy="6" r="5" fill="none" stroke="#e3161f" stroke-width="1.2"/><path d="M3.5 6.2l1.8 1.8 3.4-3.8" fill="none" stroke="#e3161f" stroke-width="1.3"/></svg>Energy-Efficient Upgrades</li>
        <li><svg class="tick" viewBox="0 0 12 12"><circle cx="6" cy="6" r="5" fill="none" stroke="#e3161f" stroke-width="1.2"/><path d="M3.5 6.2l1.8 1.8 3.4-3.8" fill="none" stroke="#e3161f" stroke-width="1.3"/></svg>Deck &amp; Patio Construction</li>
        <li><svg class="tick" viewBox="0 0 12 12"><circle cx="6" cy="6" r="5" fill="none" stroke="#e3161f" stroke-width="1.2"/><path d="M3.5 6.2l1.8 1.8 3.4-3.8" fill="none" stroke="#e3161f" stroke-width="1.3"/></svg>Water &amp; Mold Damage</li>
        <li><svg class="tick" viewBox="0 0 12 12"><circle cx="6" cy="6" r="5" fill="none" stroke="#e3161f" stroke-width="1.2"/><path d="M3.5 6.2l1.8 1.8 3.4-3.8" fill="none" stroke="#e3161f" stroke-width="1.3"/></svg>Garage Renovation</li>
      </ul>
    </div>
  </section>

  <section class="card card--contact" aria-label="Business card, contact side">
    <div class="person">
      <h1 class="person__name">Marcus Delling</h1>
      <p class="person__title">Licensed General Contractors</p>
    </div>
    <span class="divider"></span>
    <ul class="contacts">
      <li><svg viewBox="0 0 16 16"><path d="M4 1.5l2.3 3-1.4 1.6c.8 1.8 2.2 3.2 4 4l1.6-1.4 3 2.3-1.3 2.3C7.5 13.6 2.4 8.5 1.7 3.8z" fill="#e3161f"/></svg>858-471-6093</li>
      <li><svg viewBox="0 0 16 16"><rect x="1.5" y="3.5" width="13" height="9" rx="1" fill="#e3161f"/><path d="M2 4.2l6 4.6 6-4.6" fill="none" stroke="#202024" stroke-width="1.2"/></svg>info@brightoakbuilders.com</li>
      <li><svg viewBox="0 0 16 16"><circle cx="8" cy="8" r="6.5" fill="#e3161f"/><path d="M1.5 8h13M8 1.5c-2.5 3-2.5 10 0 13M8 1.5c2.5 3 2.5 10 0 13" fill="none" stroke="#202024" stroke-width="1"/></svg>www.brightoakbuilders.com</li>
    </ul>
    <p class="company">Harborline Builders Inc.</p>
  </section>

</main>
</body>
</html>
```